Alaska Law Firm Needs a Sticker Design

We need a design for stickers to put on already-printed brochures. We mail the brochures to potential clients so they can learn more about accident-induced injuries, insurance claims, legal representation, and our own law firm.

One of our lawyers wrote a book that provides a helpful overview of personal injury claims. We are offering this book for free to anyone who calls and requests it. Therefore, the sticker design should include one of the following phrases, or something very similar:
a) "Still have questions? Call and request our book-- for free!"
b) "Still have questions about auto accident claims? Call and request our book today."
c) "Still have questions about filing a claim? Call and request a free copy of our book."
d) "Still have questions? Call us today to request a free copy of our book, Clear Lanes Ahead."
e) "To learn more about automobile accidents and insurance, call today and request a free copy of our book."

The sticker should be approximately 3"x3" and may be a circle, square, rectangle, or ellipsis. The sticker will be placed on the back of the folder, which is light blue. We would like the sticker to match the color scheme of our website and the folder.

I will upload an image of the book cover as soon as I obtain it.

Law Firm

Font styles to use
Serif
Sans Serif

Requirements
Should not have
• Bright colors that aren't already used in the folder design. e.g. no bright orange, pink, chartreuse, turquoise, yellow, red.

```html
<!DOCTYPE html>
<html lang="en">
<head>
<meta charset="utf-8">
<title>Clear Lanes Ahead – Free Book Sticker</title>
<link rel="stylesheet" href="https://fonts.googleapis.com/css2?family=Bebas+Neue&family=Montserrat:wght@400;600;800&family=Poppins:wght@500&display=swap">
<style>
  :root {
    --page-bg: #e8e8e8;
    --sticker-fill: #d9e6f6;
    --sticker-edge: #ffffff;
    --navy: #143d66;
    --navy-deep: #0f1f4a;
    --ink: #111111;
    --white: #ffffff;
    --photo-top: #dfe9ef;
    --photo-mid: #9fbf86;
    --photo-low: #6f9c4a;
  }
  * { margin: 0; padding: 0; box-sizing: border-box; }
  html, body { width: 1200px; height: 855px; overflow: hidden; background: var(--page-bg); }
  .canvas { position: relative; width: 1200px; height: 855px; }

  .sticker {
    position: absolute; left: 264px; top: 108px; width: 672px; height: 672px;
    border-radius: 50%; background: var(--sticker-fill);
    border: 12px solid var(--sticker-edge); overflow: hidden;
    box-shadow: 0 4px 18px rgba(0,0,0,.12);
  }
  .sticker__band {
    position: absolute; left: 0; right: 0; top: 442px; height: 144px;
    background: var(--navy);
  }

  .headline, .offer, .phone { position: absolute; left: 0; width: 1200px; text-align: center; }
  .headline__main {
    top: 162px; font-family: "Bebas Neue", sans-serif; font-size: 98px; line-height: 1;
    color: var(--navy); letter-spacing: 1px;
  }
  .headline__sub {
    top: 252px; font-family: "Bebas Neue", sans-serif; font-size: 58px; line-height: 1;
    color: var(--white); -webkit-text-stroke: 2px var(--navy); letter-spacing: 15px;
    padding-left: 15px;
  }

  .book { position: absolute; background: var(--white); overflow: hidden; }
  .book--side { top: 350px; width: 126px; height: 176px; filter: blur(1.6px); opacity: .9; }
  .book--left { left: 472px; }
  .book--right { left: 594px; }
  .book--front { left: 524px; top: 318px; width: 156px; height: 240px; box-shadow: 0 2px 8px rgba(0,0,0,.18); }

  .book__author {
    font-family: "Montserrat", sans-serif; font-weight: 400; font-size: 9px; color: var(--navy-deep);
    text-align: center; padding-top: 11px; letter-spacing: .2px;
  }
  .book__title {
    font-family: "Montserrat", sans-serif; font-weight: 800; font-size: 17px; line-height: 1.05;
    color: var(--navy-deep); text-align: center; margin-top: 6px;
  }
  .book--side .book__author { font-size: 6px; padding-top: 8px; }
  .book--side .book__title { font-size: 12px; margin-top: 4px; }
  .book__photo {
    position: absolute; left: 3px; right: 3px; top: 76px; bottom: 26px;
    background: linear-gradient(180deg, var(--photo-top) 0%, var(--photo-mid) 55%, var(--photo-low) 100%);
  }
  .book--side .book__photo { top: 56px; bottom: 20px; }
  .book__strip {
    position: absolute; left: 3px; right: 3px; bottom: 3px; height: 24px;
    background: var(--navy-deep); color: var(--white);
    font-family: "Montserrat", sans-serif; font-weight: 600; font-size: 7px; line-height: 1.25;
    text-align: center; padding-top: 4px;
  }
  .book--side .book__strip { height: 18px; font-size: 5px; padding-top: 3px; }

  .offer__lead {
    top: 572px; font-family: "Bebas Neue", sans-serif; font-size: 38px; line-height: 1;
    color: var(--white); letter-spacing: .5px;
  }
  .offer__free {
    top: 612px; font-family: "Bebas Neue", sans-serif; font-size: 94px; line-height: 1;
    color: var(--white); letter-spacing: 1px;
  }
  .phone {
    top: 712px; font-family: "Poppins", sans-serif; font-weight: 500; font-size: 29px; line-height: 1.2;
    color: var(--ink);
  }
</style>
</head>
<body>
<div class="canvas">
  <div class="sticker">
    <div class="sticker__band"></div>
  </div>

  <h1 class="headline headline__main">Still Have</h1>
  <p class="headline headline__sub">Questions?</p>

  <div class="book book--side book--left">
    <p class="book__author">DANIEL R. MERCER</p>
    <p class="book__title">CLEAR LANES<br>AHEAD</p>
    <div class="book__photo" role="img" aria-label="Cover photo of a smiling family lying on the grass beside a small car"></div>
    <p class="book__strip">THE RIGHT WAY TO HANDLE<br>YOUR AUTO ACCIDENT CLAIM</p>
  </div>
  <div class="book book--side book--right">
    <p class="book__author">DANIEL R. MERCER</p>
    <p class="book__title">CLEAR LANES<br>AHEAD</p>
    <div class="book__photo" role="img" aria-label="Cover photo of a smiling family lying on the grass beside a small car"></div>
    <p class="book__strip">THE RIGHT WAY TO HANDLE<br>YOUR AUTO ACCIDENT CLAIM</p>
  </div>
  <div class="book book--front">
    <p class="book__author">DANIEL R. MERCER</p>
    <p class="book__title">CLEAR LANES<br>AHEAD</p>
    <div class="book__photo" role="img" aria-label="Cover photo of a smiling family lying on the grass beside a small red car"></div>
    <p class="book__strip">THE RIGHT WAY TO HANDLE<br>YOUR AUTO ACCIDENT CLAIM</p>
  </div>

  <p class="offer offer__lead">Call &amp; Request Our Book</p>
  <p class="offer offer__free">For Free !!</p>
  <p class="phone">(907) 555-0148</p>
</div>
</body>
</html>
```